Business Card Design

Business Card for professional consulting firm working with large financial institutions.

Target Market(s)

Executive buyers

Industry/Entity Type

Banking

Contact Information for Business Card

Mild creativity wanted. Not boring, but do elaborate artwork.

Font styles to use
Serif
Sans Serif

Colors

Designer to choose colors to be used in the design.

Requirements
Must have
• Standard business card features - company name, individual name, telephone, website, email, locations.
Nice to have
• Two colors
Should not have
• too many colors, fancy printing, cartoons.

```html
<!DOCTYPE html>
<html lang="en">
<head>
<meta charset="UTF-8">
<title>Northvale Advisory – Business Card</title>
<link rel="stylesheet" href="https://fonts.googleapis.com/css2?family=Roboto:wght@400;500;700&display=swap">
<style>
  :root {
    --stage: #262626;
    --card-back: #bcbdbf;
    --card-front: #ffffff;
    --brand-grey: #9c9da0;
    --name-grey: #b8b9bb;
    --ink: #333333;
    --ink-soft: #555555;
    --icon: #9a9a9a;
    --white: #ffffff;
  }
  * { box-sizing: border-box; margin: 0; padding: 0; }
  html, body {
    width: 1200px;
    height: 930px;
    overflow: hidden;
    background: var(--stage);
    font-family: "Roboto", Arial, sans-serif;
  }
  .stage {
    position: relative;
    width: 1200px;
    height: 930px;
  }
  .card {
    position: absolute;
    width: 560px;
    height: 320px;
    border-radius: 18px;
    box-shadow: 0 14px 30px rgba(0,0,0,0.45);
  }
  /* Back side */
  .card--back {
    left: 90px;
    top: 100px;
    background: var(--card-back);
    display: flex;
    align-items: center;
    justify-content: center;
  }
  .brand {
    display: flex;
    align-items: center;
    gap: 12px;
    font-weight: 500;
    letter-spacing: 0.5px;
  }
  .brand__dot {
    width: 14px;
    height: 14px;
    border-radius: 50%;
    background: currentColor;
  }
  .card--back .brand {
    color: var(--white);
    font-size: 36px;
  }
  .card--back .brand__dot { width: 20px; height: 20px; }

  /* Front side */
  .card--front {
    left: 550px;
    top: 500px;
    background: var(--card-front);
  }
  .card--front .brand {
    position: absolute;
    left: 38px;
    top: 46px;
    color: var(--brand-grey);
    font-size: 22px;
  }
  .person {
    position: absolute;
    right: 40px;
    top: 70px;
    text-align: right;
  }
  .person__name {
    font-size: 24px;
    font-weight: 700;
    color: var(--name-grey);
    letter-spacing: 0.5px;
  }
  .person__role {
    font-size: 13px;
    color: var(--ink);
    margin-top: 2px;
  }
  .rule {
    position: absolute;
    height: 2px;
    background: var(--ink);
  }
  .rule--main { left: 32px; right: 32px; top: 128px; }
  .rule--contact { left: 38px; width: 210px; top: 228px; }
  .address {
    position: absolute;
    right: 40px;
    top: 150px;
    text-align: right;
    font-size: 14px;
    line-height: 1.45;
    color: var(--ink-soft);
    font-style: normal;
  }
  .contact {
    position: absolute;
    left: 38px;
    top: 244px;
    list-style: none;
    font-size: 14px;
    line-height: 21px;
    color: var(--ink);
  }
  .contact__item {
    display: flex;
    align-items: center;
    gap: 9px;
  }
  .contact__icon {
    width: 11px;
    height: 11px;
    flex: none;
    fill: none;
    stroke: var(--icon);
    stroke-width: 1.4;
  }
</style>
</head>
<body>
<main class="stage">
  <section class="card card--back" aria-label="Card back">
    <div class="brand"><span class="brand__dot"></span>Northvale Advisory</div>
  </section>

  <section class="card card--front" aria-label="Card front">
    <div class="brand"><span class="brand__dot"></span>Northvale Advisory</div>

    <div class="person">
      <div class="person__name">DANIEL HARPER</div>
      <div class="person__role">Director</div>
    </div>

    <div class="rule rule--main"></div>

    <address class="address">48 Calder Ln,<br>Benalla VIC 3672</address>

    <div class="rule rule--contact"></div>

    <ul class="contact">
      <li class="contact__item">
        <svg class="contact__icon" viewBox="0 0 12 12"><path d="M2.5 1.5 L4.5 1.5 L5.2 3.8 L4 4.8 C4.7 6.3 5.7 7.3 7.2 8 L8.2 6.8 L10.5 7.5 L10.5 9.5 C10.5 10.2 9.9 10.6 9.2 10.5 C5 10 2 7 1.5 2.8 C1.4 2.1 1.8 1.5 2.5 1.5 Z"/></svg>
        +330 2460-5172
      </li>
      <li class="contact__item">
        <svg class="contact__icon" viewBox="0 0 12 12"><rect x="1" y="2.5" width="10" height="7"/><path d="M1 2.5 L6 6.5 L11 2.5"/></svg>
        info@northvaleadvisory.com
      </li>
      <li class="contact__item">
        <svg class="contact__icon" viewBox="0 0 12 12"><circle cx="6" cy="6" r="4.8"/><ellipse cx="6" cy="6" rx="2" ry="4.8"/><path d="M1.2 6 H10.8"/></svg>
        www.northvaleadvisory.com
      </li>
    </ul>
  </section>
</main>
</body>
</html>
```